Website redesign www.marigoldlawpc.com law firm site

Need to redesign the website that I currently have to look more modern and professional. Would also like to be able to make updates and post without having a huge hassle. See current www.marigoldlawpc.com. I just think that it looks very immature and it's very templated there's no ability for me to make posts or Add links or anything like that

Target Market(s)

California people looking for a powerhouse attorney in

Industry/Entity Type

Legal

Number of Pages Required

3 page

Font styles to use
Serif
Sans Serif

Colors
ec1f27
000000
ffffff

Requirements
Must have
• Must be mobile friendly. Must look professional and have ability to post links to other websites. Must have ability to post blogs or articles. Would like to be able to read my FeeTrove account and also have the ability to upload forms for people to download
Nice to have
• Simple design easy to use and not cluttered with too much text

```html
<!DOCTYPE html>
<html lang="en">
<head>
<meta charset="utf-8">
<title>Marigold Law, P.C. — Chico California Attorney</title>
<link rel="stylesheet" href="https://fonts.googleapis.com/css2?family=Open+Sans:ital,wght@0,400;0,600;0,700;1,400&display=swap">
<style>
:root{
  --red:#ec1f27;
  --black:#000000;
  --white:#ffffff;
  --ink:#222222;
  --text:#555555;
  --muted:#777777;
  --dark:#262626;
  --footer:#2b2b2b;
  --footer-bar:#222222;
}
*{box-sizing:border-box;margin:0;padding:0}
html,body{width:1200px;height:3291px;overflow:hidden}
body{font-family:"Open Sans",Arial,sans-serif;color:var(--text);background:var(--white)}
.container{width:1002px;margin:0 auto;position:relative}
.btn{display:inline-block;background:var(--red);color:var(--white);font-weight:700;font-size:13px;text-transform:uppercase;letter-spacing:.3px;border-radius:22px;padding:12px 44px;text-decoration:none}
.btn-square{border-radius:2px;padding:14px 32px}
.section-title{text-align:center;font-size:26px;font-weight:700;color:var(--ink);text-transform:uppercase;letter-spacing:.3px}
.title-rule{width:42px;height:3px;background:var(--red);margin:14px auto 18px}
.section-sub{text-align:center;font-size:13px;color:var(--muted)}

/* header */
.site-header{height:81px;position:relative}
.brand{position:absolute;left:116px;top:22px;text-decoration:none;font-size:28px;font-weight:400;color:var(--red);line-height:1.2}
.main-nav{position:absolute;right:99px;top:33px;display:flex;gap:56px}
.main-nav a{font-size:11.5px;color:var(--ink);text-decoration:none;text-transform:uppercase;letter-spacing:.3px}

/* hero */
.hero{height:498px;position:relative;background:linear-gradient(90deg,#2a2522 0%,#4a3d35 35%,#6b5a4d 55%,#c9b8a6 75%,#3a3330 100%)}
.hero-photo{position:absolute;inset:0}
.hero-copy{position:absolute;left:99px;top:106px;width:480px;color:var(--white)}
.hero-copy h1{font-size:36px;font-weight:700;line-height:1.15;text-transform:uppercase}
.hero-copy h2{font-size:33px;font-weight:400;line-height:1.2;text-transform:uppercase;margin-bottom:18px}
.hero-copy p{font-size:14px;line-height:1.85;margin-bottom:24px}
.hero-dots{position:absolute;left:573px;bottom:28px;display:flex;gap:6px}
.hero-dots span{width:7px;height:7px;border-radius:50%;background:rgba(255,255,255,.5)}
.hero-dots span.active{background:var(--red)}

/* welcome */
.welcome{height:246px;background:var(--dark);color:var(--white);text-align:center;padding-top:52px}
.welcome h2{font-size:29px;font-weight:700;text-transform:uppercase;margin-bottom:26px}
.welcome p{width:900px;margin:0 auto;font-size:11.5px;line-height:2.1;color:#e6e6e6}

/* practice */
.practice{height:658px;padding-top:56px}
.card-row{display:flex;gap:14px;margin-top:31px}
.practice-card{width:325px}
.practice-img{height:204px}
.card-title{font-size:15px;font-weight:700;color:var(--ink);text-transform:uppercase;margin:20px 0 10px}
.card-text{font-size:13px;line-height:1.8;color:var(--text)}
.center-btn{text-align:center;margin-top:30px}

/* about */
.about{height:404px;display:flex}
.about-img{width:600px;height:100%;background:linear-gradient(135deg,#3b4a58 0%,#8b95a0 40%,#d6cfc7 65%,#6a7380 100%)}
.about-body{width:600px;background:var(--dark);color:var(--white);text-align:right;padding:86px 88px 0 60px}
.about-body h2{font-size:29px;font-weight:700;text-transform:uppercase;margin-bottom:20px}
.about-body p{font-size:11.5px;line-height:2.1;color:#cfcfcf;margin-bottom:16px}

/* blog */
.blog{height:658px;padding-top:68px}
.blog-row{display:flex;gap:40px;margin-top:40px}
.blog-card{width:307px}
.blog-img{height:150px}
.blog-card .card-title{line-height:1.75;margin:74px 0 26px;font-size:14.5px}
.blog-card .card-text{font-size:13px;line-height:2.35}

/* testimonials */
.testimonials{height:421px;padding-top:20px}
.testimonial{position:relative;margin-top:56px;height:200px}
.avatar{position:absolute;left:60px;top:0;width:189px;height:189px;border-radius:50%;background:radial-gradient(circle at 50% 45%,#b59b86 0%,#8a7565 45%,#cfd3d6 100%)}
.quote-mark{position:absolute;font-size:48px;color:#cccccc;line-height:1}
.quote-open{left:310px;top:-6px}
.quote-close{left:920px;top:74px}
.quote{position:absolute;left:349px;top:14px;width:600px;font-style:italic;font-size:13px;line-height:2;color:var(--muted)}
.quote-author{position:absolute;left:349px;top:126px;font-size:14px;font-weight:700;color:var(--red)}
.quote-nav{position:absolute;left:908px;top:144px;display:flex;gap:4px}

/* footer */
.site-footer{height:264px;background:var(--footer);color:#bbbbbb;position:relative}
.footer-col{position:absolute;top:44px}
.footer-col h4{font-size:13px;font-weight:700;color:var(--white);text-transform:uppercase;margin-bottom:18px}
.footer-col p,.footer-col li{font-size:11.5px;line-height:2.35;list-style:none}
.footer-about{left:103px;width:340px}
.footer-about p{line-height:2.1}
.read-more{display:flex;align-items:center;gap:8px;color:var(--white);font-weight:700;font-size:12px;margin-top:14px}
.col-welcome{left:520px}
.col-info{left:700px}
.col-contact{left:908px}
.contact-item{display:flex;align-items:flex-start;gap:10px;font-size:11.5px;line-height:1.9;margin-bottom:8px}
.contact-item svg{flex:none;margin-top:4px}
.footer-bar{height:61px;background:var(--footer-bar);color:#9a9a9a;font-size:11.5px;display:flex;align-items:center;padding:0 103px}
.footer-bar .copy{flex:1}
.social{display:flex;align-items:center;gap:22px}
.social span.dot{width:10px;height:10px;border-radius:50%;background:#9a9a9a}
</style>
</head>
<body>

<header class="site-header">
  <a class="brand" href="#">Marigold Law PC</a>
  <nav class="main-nav">
    <a href="#">Attorney Profile</a>
    <a href="#">Practice Areas</a>
    <a href="#">Client Reviews</a>
    <a href="#">Links</a>
    <a href="#">Contact Us</a>
  </nav>
</header>

<section class="hero">
  <div class="hero-photo" role="img" aria-label="Smiling attorney in a dark suit in front of a blurred office"></div>
  <div class="hero-copy">
    <h1>Marigold Law, P.C.</h1>
    <h2>Chico California Attorney</h2>
    <p>Find the big firm style legal counsel you can work with in your hometown region at Marigold Law P.C., in Chico, CA. Attorney Lena M. Hart, Esq., offers a boutique law firm opportunity for clients who want to enjoy all the advantages of her broad legal experience and education.</p>
    <a class="btn btn-square" href="#">Contact Here!</a>
  </div>
  <div class="hero-dots"><span class="active"></span><span></span><span></span><span></span></div>
</section>

<section class="welcome">
  <h2>Welcome to Marigold Law P.C</h2>
  <p>Find the big firm style legal counsel you can work with in your hometown region at Marigold Law P.C., in Chico, CA. Attorney Lena M. Hart, Esq., offers a boutique law firm opportunity for clients who want to enjoy all the advantages of her broad legal experience and education. She works closely with clients, and has the knowledge of many areas of law to apply to your situation. This is very helpful when it is necessary to incorporate those different areas of law practice into creating a winning argument for your unique case.</p>
</section>

<section class="practice">
  <div class="container">
    <h2 class="section-title">Practice Areas</h2>
    <div class="title-rule"></div>
    <p class="section-sub">Small and medium-sized businesses have many of the same legal issues that affect large businesses</p>
    <div class="card-row">
      <article class="practice-card">
        <div class="practice-img" role="img" aria-label="Business people silhouetted against glass towers" style="background:linear-gradient(180deg,#c9d6e6 0%,#8fa4bd 50%,#1e2530 100%)"></div>
        <h3 class="card-title">Business Law</h3>
        <p class="card-text">Small and medium-sized businesses have many of the same legal issues that affect large businesses, such as business structure...</p>
      </article>
      <article class="practice-card">
        <div class="practice-img" role="img" aria-label="Hands in a suit holding a small house" style="background:radial-gradient(circle at 50% 50%,#3d4f6e 0%,#1a2438 70%)"></div>
        <h3 class="card-title">Real Estate Law</h3>
        <p class="card-text">At Marigold Law P.C., we help Californians who need legal advice and representation for Real Estate Law activities...</p>
      </article>
      <article class="practice-card">
        <div class="practice-img" role="img" aria-label="Word cloud about criminal law" style="background:linear-gradient(135deg,#efe9e4 0%,#d9c6c0 50%,#efe9e4 100%)"></div>
        <h3 class="card-title">Bankruptcy</h3>
        <p class="card-text">If your finances are dwindling to the point where you can no longer pay your bills, and you are getting harassed by collection agents...</p>
      </article>
    </div>
    <div class="center-btn"><a class="btn" href="#">View More</a></div>
  </div>
</section>

<section class="about">
  <div class="about-img" role="img" aria-label="Smiling professionals seated at a meeting table"></div>
  <div class="about-body">
    <h2>About Marigold Law P.C</h2>
    <p>Find the big firm style legal counsel you can work with in your hometown region at Marigold Law P.C., in Chico, CA. Attorney Lena M. Hart, Esq., offers a boutique law firm opportunity for clients who want to enjoy all the advantages of her broad legal experience and education. She works closely with clients, and has the knowledge of many areas of law to apply to your situation...</p>
    <a class="btn" href="#">View More</a>
  </div>
</section>

<section class="blog">
  <div class="container">
    <h2 class="section-title">Blog Posts</h2>
    <div class="title-rule"></div>
    <p class="section-sub">Small and medium-sized businesses have many of the same legal issues that affect large businesses</p>
    <div class="blog-row">
      <article class="blog-card">
        <div class="blog-img" role="img" aria-label="Hand signing a document beside law books" style="background:linear-gradient(135deg,#6e1d1a 0%,#b98a72 45%,#efe6dc 100%)"></div>
        <h3 class="card-title">Businesses and individuals in the areas of business law</h3>
        <p class="card-text">Es simplemente el texto de relleno de las imprentas y archivos de texto. Lorem Ipsum ha sido el texto de relleno estándar de las industrias desde el año 1500, cuando un impresor...</p>
      </article>
      <article class="blog-card">
        <div class="blog-img" role="img" aria-label="Stone courthouse facade engraved with the word justice" style="background:linear-gradient(180deg,#8a7358 0%,#c8b08d 50%,#5a4633 100%)"></div>
        <h3 class="card-title">Businesses and individuals in the areas of business law</h3>
        <p class="card-text">Es simplemente el texto de relleno de las imprentas y archivos de texto. Lorem Ipsum ha sido el texto de relleno estándar de las industrias desde el año 1500, cuando un impresor...</p>
      </article>
      <article class="blog-card">
        <div class="blog-img" role="img" aria-label="Woman working on a laptop on a sofa" style="background:linear-gradient(135deg,#4a3b30 0%,#b39a84 50%,#e3d8cc 100%)"></div>
        <h3 class="card-title">Businesses and individuals in the areas of business law</h3>
        <p class="card-text">Es simplemente el texto de relleno de las imprentas y archivos de texto. Lorem Ipsum ha sido el texto de relleno estándar de las industrias desde el año 1500, cuando un impresor...</p>
      </article>
    </div>
  </div>
</section>

<section class="testimonials">
  <div class="container">
    <h2 class="section-title">What Our Client’s Say</h2>
    <div class="title-rule"></div>
    <p class="section-sub">Small and medium-sized businesses have many of the same legal issues that affect large businesses</p>
    <div class="testimonial">
      <div class="avatar" role="img" aria-label="Portrait of a client in a suit"></div>
      <span class="quote-mark quote-open">“</span>
      <p class="quote">Marigold Law has met and exceeded our expectations in assisting our company with our real estate legal needs. In an area of law where the rules our ever changing, we simply could not navigate our company effectively without their help...</p>
      <span class="quote-mark quote-close">”</span>
      <div class="quote-author">Alder Commercial</div>
      <div class="quote-nav">
        <svg width="12" height="12" viewBox="0 0 12 12"><circle cx="6" cy="6" r="6" fill="#cccccc"/><path d="M7 3.5 4.5 6 7 8.5" stroke="#fff" stroke-width="1.5" fill="none"/></svg>
        <svg width="12" height="12" viewBox="0 0 12 12"><circle cx="6" cy="6" r="6" fill="#cccccc"/><path d="M5 3.5 7.5 6 5 8.5" stroke="#fff" stroke-width="1.5" fill="none"/></svg>
      </div>
    </div>
  </div>
</section>

<footer class="site-footer">
  <div class="footer-col footer-about">
    <h4>Who We Are?</h4>
    <p>Find the big firm style legal counsel you can work with in your hometown region at Marigold Law P.C., in Chico, CA. Attorney Lena M. Hart, Esq., offers a boutique law firm opportunity for clients who want to enjoy all the advantages of her broad legal experience and education...</p>
    <div class="read-more">Read more info
      <svg width="12" height="12" viewBox="0 0 12 12"><circle cx="6" cy="6" r="6" fill="#ffffff"/><path d="M5 3.5 7.5 6 5 8.5" stroke="#2b2b2b" stroke-width="1.5" fill="none"/></svg>
    </div>
  </div>
  <div class="footer-col col-welcome">
    <h4>Welcome</h4>
    <ul><li>Home</li><li>Attorney Profile</li><li>Practice Areas</li><li>Client Reviews</li><li>Links</li><li>Contact Us</li></ul>
  </div>
  <div class="footer-col col-info">
    <h4>Information</h4>
    <ul><li>Terms &amp; Conditions</li><li>Privacy policy</li><li>Disclaimer</li><li>Contact us</li><li>Sitemap</li></ul>
  </div>
  <div class="footer-col col-contact">
    <h4>Contact Info</h4>
    <div class="contact-item">
      <svg width="10" height="13" viewBox="0 0 10 13"><path d="M5 0C2.2 0 0 2.2 0 5c0 3.5 5 8 5 8s5-4.5 5-8c0-2.8-2.2-5-5-5zm0 7a2 2 0 1 1 0-4 2 2 0 0 1 0 4z" fill="#bbbbbb"/></svg>
      <span>410 Oak Lane<br>Suite 12, Chico, CA 95926</span>
    </div>
    <div class="contact-item">
      <svg width="11" height="11" viewBox="0 0 11 11"><path d="M2.2 0 4 2.6 2.9 4c.7 1.5 2.1 2.9 3.6 3.6L7.9 6.5 10.5 8.3 9.3 10.6C4.6 10.2.4 6 0 1.3z" fill="#bbbbbb"/></svg>
      <span>(555) 014-2231</span>
    </div>
    <div class="contact-item">
      <svg width="11" height="11" viewBox="0 0 11 11"><path d="M2.2 0 4 2.6 2.9 4c.7 1.5 2.1 2.9 3.6 3.6L7.9 6.5 10.5 8.3 9.3 10.6C4.6 10.2.4 6 0 1.3z" fill="#bbbbbb"/></svg>
      <span>(555) 017-8830</span>
    </div>
    <div class="contact-item">
      <svg width="12" height="9" viewBox="0 0 12 9"><rect width="12" height="9" rx="1" fill="#bbbbbb"/><path d="M0.5 0.8 6 5 11.5 0.8" stroke="#2b2b2b" stroke-width="1.2" fill="none"/></svg>
      <span>lena@marigoldlawgroup.com</span>
    </div>
  </div>
</footer>
<div class="footer-bar">
  <span class="copy">© 2016. Marigold Law. All rights reserved</span>
  <div class="social">
    <span>Connect with our social network :</span>
    <span class="dot"></span><span class="dot"></span><span class="dot"></span><span class="dot"></span><span class="dot"></span>
  </div>
</div>

</body>
</html>
```